I would like a business card to match my truck wrap and logo. I would like the font to match my existing business card please.

Industry/Entity Type

Painter

Contact Information for Business Card

Rodrigo Fenwar 801-437-2190 Fenwarcoatings.utah@brelmox.com
SERVICES - Custom Paint & Stain, Interior & Exterior, Epoxy Coatings / Garage Floors, Cabinet Refinishing, Log Staining and Refinishing.

Requirements
Nice to have
• I would like to have the white and grey line like the bottom of my vehicle wrap, Light Grey to match my truck also.

```html
<!DOCTYPE html>
<html lang="en">
<head>
<meta charset="utf-8">
<title>Fenwar Coatings – Business Card</title>
<link rel="stylesheet" href="https://fonts.googleapis.com/css2?family=Russo+One&family=Roboto:wght@400;700&display=swap">
<style>
  :root {
    --bg: #2a2a2c;
    --card-white: #ffffff;
    --brand-blue: #08a6e8;
    --deep-blue: #0b5fa6;
    --bright-blue: #05b0f2;
    --rule-grey: #8a8a8a;
    --text-white: #ffffff;
  }
  * { box-sizing: border-box; margin: 0; padding: 0; }
  html, body {
    width: 1200px; height: 1108px; overflow: hidden;
    background: var(--bg);
  }
  .stage {
    width: 1200px; height: 1108px;
    display: flex; align-items: center; justify-content: center; gap: 70px;
  }
  .card {
    width: 380px; height: 650px;
    border-radius: 22px;
    position: relative;
    overflow: hidden;
    box-shadow: 0 18px 40px rgba(0,0,0,.45);
  }
  /* Front */
  .card-front {
    background: var(--card-white);
    display: flex; flex-direction: column; align-items: center;
  }
  .brand-mark {
    margin-top: 150px;
    display: flex; flex-direction: column; align-items: center; gap: 6px;
    font-family: "Russo One", sans-serif;
    color: var(--brand-blue);
    font-size: 50px; line-height: 1;
    letter-spacing: 1px;
    text-transform: uppercase;
  }
  .contact {
    position: absolute; left: 0; right: 0; bottom: 80px;
    text-align: center;
    font-family: "Russo One", sans-serif;
    color: var(--brand-blue);
  }
  .contact-name { font-size: 27px; letter-spacing: .5px; }
  .contact-rule {
    width: 120px; height: 1px; background: var(--rule-grey);
    margin: 12px auto 10px;
  }
  .contact-phone { font-size: 25px; margin-bottom: 6px; }
  .contact-email { font-size: 16.5px; }
  /* Back */
  .card-back {
    background: linear-gradient(180deg, var(--bright-blue) 0%, var(--brand-blue) 45%, var(--deep-blue) 100%);
    color: var(--text-white);
    display: flex; flex-direction: column; align-items: center;
  }
  .back-pattern {
    position: absolute; inset: 0;
    background: linear-gradient(160deg, rgba(255,255,255,.06), rgba(0,0,0,.06));
  }
  .back-mark {
    position: relative;
    margin-top: 300px;
    display: flex; align-items: center; gap: 10px;
    font-family: "Russo One", sans-serif;
    font-size: 22px; letter-spacing: 1px;
    text-transform: uppercase;
  }
  .back-mark-square { width: 22px; height: 22px; background: var(--text-white); }
  .services {
    position: relative;
    margin-top: 30px;
    text-align: center;
    font-family: "Roboto", sans-serif;
  }
  .services-title { font-weight: 700; font-size: 24px; margin-bottom: 6px; }
  .services-list { list-style: none; font-size: 20px; line-height: 1.45; }
</style>
</head>
<body>
<main class="stage">
  <section class="card card-front">
    <div class="brand-mark">
      <span>Fenwar</span>
      <span>Coatings</span>
    </div>
    <div class="contact">
      <p class="contact-name">RODRIGO FENWAR</p>
      <div class="contact-rule"></div>
      <p class="contact-phone">801-437-2190</p>
      <p class="contact-email">Fenwarcoatings.utah@brelmox.com</p>
    </div>
  </section>

  <section class="card card-back">
    <div class="back-pattern" role="img" aria-label="Faint repeating brand pattern on blue background"></div>
    <div class="back-mark">
      <span class="back-mark-square"></span>
      <span>Fenwar Coatings</span>
    </div>
    <div class="services">
      <h2 class="services-title">SERVICES</h2>
      <ul class="services-list">
        <li>Custom Paint &amp; Stain</li>
        <li>Interior &amp; Exterior</li>
        <li>Epoxy Coatings / Garage Floors</li>
        <li>Cabinet Refinishing</li>
        <li>Log Staining and Refinishing.</li>
      </ul>
    </div>
  </section>
</main>
</body>
</html>
```